Doctor to Patient Management Website

I need a design for a health management website that connects doctors to patients. The website will consist of: A main page mainly describing our goal, services, and initiatives towards (Who we are AKA "About Us", Our services, Contact Us, Quick Links for health tips, Language selection, Find a doctor, search bar, Member Login Section, small glossary section below with links to all entities mentioned prior, Help section (Helpful tips and tutorials, Used to request help from admin, customer service, to resolve issues or get assistance). A profile page with two types:1) Doctor Profile: Doctor Personal info (First, Last, Middle Name, Title), Clinic, Hospital Info, Department, Credentials, Years of Experience, Patients rating, #Patients seen during the current week, #Patients seen in total, Picture, Link to email doctor, Link to print doctor's profile). Tabs for "About Me", "Contact Info", "Ratings & Comments", "Documents" (To be downloaded and uploaded by patient), "Patients (List of Patients alphabetical order by name)", "Calendar" (to see doctor's availability for booking) underneath all links. 2) Patient profile: About me, Personal Info, Height, Weight, Blood Type, Age, DOB, Name, etc..., Message and email link.Picture of patient with menu made of "Personal Data", "Biometrics", "Allergies", "Illnesses", "Medications", "Medical Procedures", "Doctors" treating the patient, "Documents" (To be downloaded and uploaded by patient). Underneath all, other patients he or she is related to (For example: family member, so patient can't connect to other patients who are family members)3) Login section: New Users will have option to register using:First Name (Required), Last Name, Middle (not required), Address (Not required), City (Required), Country (Required), Email (Not required), Phone Number (Required), Choose UserName, Password, Account Type (Doctor or Patient). Once registered, they will log in using UserName, Password, and Account_Type.Curent Users will log in using UserName, Password, and Account_Type and option to retrieve username or password.Pages to include (Login Page - Registration Page - Retrieve Username and Reset Password Page)Please see link below:https://plumcrate-adwerks.net/importance-claiming-vantorix-quibble-zarn/Pictures are attached to this project as an inspirationFYI: Dummy text can be used to fill in the business, services, and descriptive information. Feel free to include your own ideas in the layout, design, categories, patterns, and more to and showcase your talent. Design and pictures provided are available as source of ideas.

Target Market(s)

Age: 21+ / Family Oriented / Medical Sector / Metropolitan Area / Educated and non Educated Users

Industry/Entity Type

Health Care

Number of Pages Required

5+ page

Font styles to use
Sans Serif

Colors

Designer to choose colors to be used in the design.

Requirements
Must have
• Thin layer design
• Simple font - No serif
• Clean menu with light but solid colors (No Gradient effect)
Nice to have
• Different color themes (2 or 3) can be combined
• Sample pictures for illustration (either as an ad or to go with the flow of your design)
• Dashboard Feel (Suggested but not required)
Should not have
• Artistic fonts - with Serif
• Dark color themes

```html
<!DOCTYPE html>
<html lang="en">
<head>
<meta charset="utf-8">
<title>VITANOR – Find a Doctor</title>
<link href="https://fonts.googleapis.com/css2?family=Roboto:wght@400;500;700;900&display=swap" rel="stylesheet">
<style>
:root{
  --blue:#1a6bb5;
  --blue-dark:#12528f;
  --blue-bright:#2b8fe0;
  --green:#5aa532;
  --ink:#1b1b1b;
  --text:#555;
  --muted:#888;
  --line:#cfcfcf;
  --grey-bg:#f2f2f2;
  --white:#fff;
}
*{box-sizing:border-box;margin:0;padding:0}
html,body{width:1200px;height:5114px;overflow:hidden;background:var(--white);font-family:"Roboto",Arial,sans-serif;color:var(--text)}
.page{position:relative;width:1200px;height:5114px}
.abs{position:absolute}

/* header */
.site-header{position:absolute;left:0;top:0;width:1200px;height:100px;background:var(--white);z-index:3}
.brand{position:absolute;left:140px;top:0;width:170px;height:160px;border-radius:0 0 85px 85px;background:var(--white);display:flex;flex-direction:column;align-items:center;justify-content:flex-end;padding-bottom:22px;z-index:4}
.brand-dot{width:54px;height:54px;border-radius:50%;background:var(--green);margin-bottom:10px}
.brand-name{font-weight:700;font-size:22px;color:var(--blue);letter-spacing:1px}
.main-nav{position:absolute;left:420px;top:45px;display:flex;gap:14px;font-size:14px;font-weight:500;color:var(--ink)}
.main-nav a{color:inherit;text-decoration:none}
.btn-login{position:absolute;left:840px;top:38px;width:100px;height:32px;border-radius:16px;background:var(--blue);color:#fff;font-size:12px;font-weight:700;display:flex;align-items:center;justify-content:center}
.btn-register{position:absolute;left:957px;top:38px;width:126px;height:32px;border-radius:16px;border:2px solid var(--green);color:var(--green);font-size:12px;font-weight:700;display:flex;align-items:center;justify-content:center}
.lang{position:absolute;left:1124px;top:45px;font-size:14px;font-weight:700;color:var(--ink)}

/* hero */
.hero{position:absolute;left:0;top:100px;width:1200px;height:560px;overflow:hidden}
.hero-photo{position:absolute;inset:0;background:linear-gradient(90deg,#6f7f93 0%,#9aa7b6 45%,#c9d1da 75%,#aeb8c4 100%)}
.hero-kicker{position:absolute;left:150px;top:130px;color:#fff;font-size:30px;font-weight:700;letter-spacing:3px}
.hero-title{position:absolute;left:150px;top:175px;color:var(--blue);font-size:62px;font-weight:900;letter-spacing:5px}
.hero-tag{position:absolute;left:160px;top:268px;color:#fff;font-size:20px}
.search{position:absolute;left:145px;top:330px;width:465px;height:50px;border-radius:25px;background:#fff;display:flex;align-items:center;padding-left:40px;font-size:15px;font-style:italic;color:#888}
.search-btn{position:absolute;right:4px;top:6px;width:130px;height:38px;border-radius:19px;background:var(--blue);color:#fff;font-style:normal;font-weight:700;font-size:14px;display:flex;align-items:center;justify-content:center}
.arrow-c{position:absolute;top:225px;width:36px;height:36px;border-radius:50%;border:2px solid rgba(255,255,255,.7)}

/* section titles */
.sec-title{position:absolute;left:0;width:1200px;text-align:center;font-size:42px;font-weight:700;color:var(--ink)}
.sec-title::after{content:"";display:block;width:100px;height:3px;background:var(--blue);margin:16px auto 0}

/* services */
.service{position:absolute;top:950px;width:228px;height:200px;border:1px solid var(--line);text-align:center}
.service-hex{position:absolute;left:74px;top:-40px;width:80px;height:80px}
.service h3{margin-top:68px;font-size:14px;font-weight:500;color:var(--blue);letter-spacing:1px}
.service p{margin:24px auto 0;width:150px;font-size:11px;line-height:18px}
.service-knob{position:absolute;left:99px;bottom:-15px;width:30px;height:30px;border-radius:50%;background:#fff;border:1px solid var(--line)}
.service-knob::after{content:"";position:absolute;left:10px;top:10px;width:8px;height:8px;border-radius:50%;background:var(--green)}

/* about */
.about{position:absolute;left:0;top:1277px;width:1200px;height:515px;background:var(--grey-bg)}
.about-photo{position:absolute;left:100px;top:-30px;width:225px;height:545px;background:linear-gradient(180deg,#e7ebef,#c8d3de 60%,#b9c6d3)}
.about-title{position:absolute;left:675px;top:55px;font-size:42px;font-weight:700;color:var(--ink)}
.about-title::after{content:"";display:block;width:110px;height:3px;background:var(--blue);margin:14px 0 0 0}
.about-text{position:absolute;left:505px;top:150px;width:560px;font-size:13px;line-height:28px}
.hours-label{position:absolute;left:505px;top:305px;font-size:18px;font-weight:700;color:var(--ink);display:flex;align-items:center;gap:14px}
.hours-label::after{content:"";width:70px;height:2px;background:var(--blue)}
.hours{position:absolute;left:505px;top:340px;width:470px;border-collapse:collapse;font-size:11px;color:#fff;text-align:center}
.hours th{background:var(--blue-dark);height:34px;font-weight:700;font-size:13px}
.hours td{background:var(--blue-bright);height:34px;border-bottom:1px solid rgba(255,255,255,.25)}
.hours .emergency td{background:var(--blue-dark);height:32px;font-weight:700}

/* tips */
.tip{position:absolute;left:112px;width:986px;height:57px;border:1px solid var(--line);display:flex;align-items:center;justify-content:space-between;padding:0 36px 0 16px;font-size:17px;color:#333}
.tip-plus{color:var(--green);font-size:24px;font-weight:500}

/* doctors */
.doctor{position:absolute;top:2620px;width:304px;height:410px;border:1px solid var(--line);overflow:hidden}
.doctor-photo{position:absolute;inset:0;background:linear-gradient(180deg,#f4f6f8,#dfe6ec)}
.doctor-band{position:absolute;left:0;bottom:0;width:100%;height:80px}
.doctor-name{position:absolute;left:24px;bottom:44px;font-size:20px;font-weight:700;color:#fff}
.doctor-role{position:absolute;left:24px;bottom:24px;font-size:13px;color:#fff}

/* video */
.video{position:absolute;left:0;top:3260px;width:1200px;height:495px;background:linear-gradient(90deg,#2f3338,#5a6068 45%,#7a8088 65%,#3a3f45)}
.play{position:absolute;left:548px;top:3458px;width:104px;height:104px;border-radius:50%;background:#fff}

/* contact */
.contact-box{position:absolute;left:100px;top:3990px;width:410px;height:485px;background:var(--blue);color:#fff;padding:82px 0 0 76px}
.contact-box h4{font-size:17px;font-weight:500;letter-spacing:.5px;margin-bottom:16px}
.contact-box p{font-size:14px;line-height:28px}
.contact-box .grp{margin-bottom:28px}
.field{position:absolute;left:615px;width:395px;height:50px;border-bottom:1px solid #e3e3e3;display:flex;align-items:center;gap:18px;font-size:17px;color:#333}
.field svg{width:18px;height:18px;fill:#555}
.btn-send{position:absolute;left:612px;top:4368px;width:150px;height:34px;border-radius:17px;background:var(--green);color:#fff;font-size:11px;font-weight:700;display:flex;align-items:center;justify-content:center}

/* footer */
.footer-brand{position:absolute;left:95px;top:4770px;width:160px;text-align:center}
.footer-brand .brand-dot{width:90px;height:90px;margin:0 auto 16px}
.footer-brand span{font-size:26px;font-weight:700;color:var(--blue);letter-spacing:1px}
.fcol{position:absolute;top:4770px}
.fcol h5{font-size:18px;font-weight:700;color:var(--ink);letter-spacing:1px;margin-bottom:18px}
.fcol li{list-style:none;font-size:15px;line-height:26px;color:var(--blue-dark)}
.social li{display:flex;align-items:center;gap:12px;line-height:40px}
.social i{width:34px;height:34px;border-radius:50%;background:var(--blue);display:block}
.copy{position:absolute;left:0;top:5056px;width:1200px;text-align:center;font-size:14px;color:#555;letter-spacing:1px}
</style>
</head>
<body>
<div class="page">

<header class="site-header">
  <div class="brand"><div class="brand-dot"></div><div class="brand-name">VITANOR</div></div>
  <nav class="main-nav"><a href="#">HOME</a><a href="#">ABOUT</a><a href="#">DOCTORS</a><a href="#">VIDEOS</a><a href="#">CONTACT</a></nav>
  <div class="btn-login">&#128274; LOGIN</div>
  <div class="btn-register">&#9998; REGISTER</div>
  <div class="lang">EN &#8964;</div>
</header>

<section class="hero">
  <div class="hero-photo" role="img" aria-label="Smiling doctor in white coat pointing upward in a bright clinic"></div>
  <div class="hero-kicker">FIND A</div>
  <div class="hero-title">DOCTOR</div>
  <div class="hero-tag">we connect doctors to &nbsp;patients</div>
  <div class="search">Enter doctor name....<div class="search-btn">SEARCH</div></div>
  <div class="arrow-c" style="left:32px"></div>
  <div class="arrow-c" style="left:1132px"></div>
  <svg class="abs" style="left:0;top:380px" width="1200" height="180" viewBox="0 0 1200 180" preserveAspectRatio="none">
    <path d="M0 95 C300 20 520 20 760 90 C950 140 1100 110 1200 70 L1200 180 L0 180Z" fill="#5aa532"/>
    <path d="M0 120 C300 50 520 50 760 115 C950 165 1100 135 1200 95 L1200 180 L0 180Z" fill="#1a6bb5"/>
    <path d="M0 140 C300 75 520 80 760 140 C950 180 1100 160 1200 125 L1200 180 L0 180Z" fill="#fff"/>
  </svg>
</section>

<h2 class="sec-title" style="top:790px">SERVICES</h2>

<div class="service" style="left:110px">
  <svg class="service-hex" viewBox="0 0 80 80"><polygon points="40,2 76,21 76,59 40,78 4,59 4,21" fill="#fff" stroke="#cfcfcf"/><rect x="26" y="32" width="28" height="16" rx="2" fill="#5aa532"/></svg>
  <h3>EMERGENCY CARE</h3><p>Lorem ipsum dolor sit ametconsy elit sed do</p><div class="service-knob"></div>
</div>
<div class="service" style="left:362px">
  <svg class="service-hex" viewBox="0 0 80 80"><polygon points="40,2 76,21 76,59 40,78 4,59 4,21" fill="#fff" stroke="#cfcfcf"/><circle cx="40" cy="40" r="11" fill="#5aa532"/></svg>
  <h3>SLEEP MEDICINE</h3><p>Lorem ipsum dolor sit ametconsy elit sed do</p><div class="service-knob"></div>
</div>
<div class="service" style="left:614px">
  <svg class="service-hex" viewBox="0 0 80 80"><polygon points="40,2 76,21 76,59 40,78 4,59 4,21" fill="#fff" stroke="#cfcfcf"/><path d="M40 54 L26 40 a8 8 0 0 1 14-10 a8 8 0 0 1 14 10Z" fill="#5aa532"/></svg>
  <h3>CRITICAL CARE</h3><p>Lorem ipsum dolor sit ametconsy elit sed do</p><div class="service-knob"></div>
</div>
<div class="service" style="left:864px">
  <svg class="service-hex" viewBox="0 0 80 80"><polygon points="40,2 76,21 76,59 40,78 4,59 4,21" fill="#fff" stroke="#cfcfcf"/><ellipse cx="33" cy="42" rx="7" ry="11" fill="#5aa532"/><ellipse cx="47" cy="42" rx="7" ry="11" fill="#5aa532"/></svg>
  <h3>PULMONARY</h3><p>Lorem ipsum dolor sit ametconsy elit sed do</p><div class="service-knob"></div>
</div>

<section class="about">
  <div class="about-photo" role="img" aria-label="Doctor with stethoscope standing with arms crossed"></div>
  <h2 class="about-title">ABOUT US</h2>
  <p class="about-text">Lorem ipsum dolor sit amet, consectetur adipisicing elit, sed do eiusmod tempor incididunt ut labore et dolore magna aliqua. Ut enim ad minim veniam, quis nostrud exercitation ullamco laboris nisi ut aliquip ex ea commodo consequat endum aute.</p>
  <div class="hours-label">Working Hours</div>
  <table class="hours">
    <tr><th>DAY</th><th>OPEN</th><th>CLOSE</th></tr>
    <tr><td>MON-WED</td><td>10.00AM</td><td>10.00PM</td></tr>
    <tr><td>THU-FRI</td><td>10.00AM</td><td>10.00PM</td></tr>
    <tr><td>SAT-SUN</td><td>10.00AM</td><td>10.00PM</td></tr>
    <tr class="emergency"><td colspan="3">FOR EMERGENCY : 555 00 123</td></tr>
  </table>
</section>

<h2 class="sec-title" style="top:1870px">HEALTH TIPS</h2>
<div class="tip" style="top:2003px">Lorem Ipsum is simply dummy text of the printing and typesetting industry.<span class="tip-plus">+</span></div>
<div class="tip" style="top:2089px">At vero eos et accusamus et iusto odio dignissimos ducimus qui blanditiis pr<span class="tip-plus">+</span></div>
<div class="tip" style="top:2175px">Lorem Ipsum is simply dummy text of the printing and typesetting industry.<span class="tip-plus">+</span></div>
<div class="tip" style="top:2261px">At vero eos et accusamus et iusto odio dignissimos ducimus qui blanditiis pr<span class="tip-plus">+</span></div>
<div class="tip" style="top:2347px">Lorem Ipsum is simply dummy text of the printing and typesetting industry.<span class="tip-plus">+</span></div>

<h2 class="sec-title" style="top:2490px">OUR DOCTORS</h2>
<div class="doctor" style="left:112px">
  <div class="doctor-photo" role="img" aria-label="Portrait of male cardiologist in white coat"></div>
  <svg class="doctor-band" viewBox="0 0 304 80" preserveAspectRatio="none"><polygon points="0,0 304,0 270,80 0,80" fill="#1a6bb5"/></svg>
  <div class="doctor-name">JOHN DOE</div><div class="doctor-role">Cardiologist</div>
</div>
<div class="doctor" style="left:448px">
  <div class="doctor-photo" role="img" aria-label="Portrait of female neurologist in white coat"></div>
  <svg class="doctor-band" viewBox="0 0 304 80" preserveAspectRatio="none"><polygon points="0,0 304,0 270,80 0,80" fill="#1a6bb5"/></svg>
  <div class="doctor-name">MELISSA</div><div class="doctor-role">Nuerologist</div>
</div>
<div class="doctor" style="left:785px">
  <div class="doctor-photo" role="img" aria-label="Portrait of female cardiologist in white coat"></div>
  <svg class="doctor-band" viewBox="0 0 304 80" preserveAspectRatio="none"><polygon points="0,0 304,0 270,80 0,80" fill="#1a6bb5"/></svg>
  <div class="doctor-name">MARINA</div><div class="doctor-role">Cardiologist</div>
</div>

<h2 class="sec-title" style="top:3125px">TIPS &amp; TUTORIALS</h2>
<div class="video" role="img" aria-label="Doctor consulting a patient at a desk with laptop and stethoscope"></div>
<div class="play"><svg width="104" height="104" viewBox="0 0 104 104"><polygon points="42,32 74,52 42,72" fill="#5aa532"/></svg></div>

<h2 class="sec-title" style="top:3870px">CONTACT US</h2>
<div class="contact-box">
  <div class="grp"><h4>OUR ADDRESS</h4><p>48 Harbor Lane, Suite 210<br>Eastfield, NY 10987</p></div>
  <div class="grp"><h4>CALL US</h4><p>(555) 014-2231<br>+1 (555) 014-2232</p></div>
  <div class="grp"><h4>EMAIL US</h4><p>hello@vitanorcare.com</p></div>
</div>
<div class="field" style="top:4050px"><svg viewBox="0 0 20 20"><circle cx="10" cy="6" r="4"/><path d="M2 19a8 7 0 0 1 16 0Z"/></svg>Name</div>
<div class="field" style="top:4102px"><svg viewBox="0 0 20 20"><rect x="1" y="4" width="18" height="12"/></svg>Email</div>
<div class="field" style="top:4154px"><svg viewBox="0 0 20 20"><path d="M4 2l4 4-2 3c1 2 3 4 5 5l3-2 4 4-3 3C8 18 2 12 1 5Z"/></svg>Mobile</div>
<div class="field" style="top:4206px"><svg viewBox="0 0 20 20"><ellipse cx="10" cy="9" rx="9" ry="7"/><path d="M4 14l-1 5 5-3Z"/></svg>Message</div>
<div class="field" style="top:4280px;height:30px"></div>
<div class="btn-send">SEND MESSAGE</div>

<svg class="abs" style="left:0;top:4570px" width="1200" height="150" viewBox="0 0 1200 150" preserveAspectRatio="none">
  <path d="M0 70 C250 10 500 20 760 70 C950 105 1100 60 1200 30 L1200 80 C1100 110 950 140 760 105 C500 60 250 60 0 110Z" fill="#5aa532"/>
  <path d="M0 110 C250 60 500 60 760 105 C950 140 1100 110 1200 80 L1200 115 C1100 140 950 160 760 135 C500 100 250 95 0 140Z" fill="#1a6bb5"/>
</svg>

<div class="footer-brand"><div class="brand-dot"></div><span>VITANOR</span></div>
<div class="fcol" style="left:345px"><h5>GLOSSARY</h5><ul><li>Lorem ipsum</li><li>Excepturi oint</li><li>Lorem ipsum</li><li>Excepturi oint</li></ul></div>
<div class="fcol" style="left:645px"><h5>LINKS</h5><ul><li>Home</li><li>About us</li><li>Doctors</li><li>Contact</li></ul></div>
<div class="fcol social" style="left:880px"><h5>CONNECT WITH US</h5><ul><li><i></i>Friendlane</li><li><i></i>Chirpline</li><li><i></i>Viewtube</li><li><i></i>Callnest</li></ul></div>
<div class="copy">Copyrights 2019. All rights reserved</div>

</div>
</body>
</html>
```